Holiday Rental Company Flyer Design (DL not A5)

Note from Brandloom Administration: The category sizing selected is A5, however the project requires DL sized artwork. Please refer to the DL template link below while the 'Special Requirements' are updated accordingly.

Project Brief:
We need a double sided DL flyer designed for an up market Holiday Rental Company that portrays a personalised approach to property management. These are to be used for letter box drops to homes we're specifically targeting so the design should be modern, complimentary colour palette, uncluttered & visually appealing.

Please Download the DL Template from Quillora here: http://www.quillora.com.au/ql/ns/propath/UploadResources.aspx?selectedTab=0?pfid=KMT&pf_id=KMT&xnav=easypath-upload-image#Templates

Target Market(s)

Wealthy Home Owners

Industry/Entity Type

It Company

Other font styles liked:
• Avant Garde Extra Light & Demi

Colors
33b8a4

Requirements
Must have
• DL Flyer sizes (210mm width x 99mm width, plus 3mm bleed)
• Front: Logo, Main Image & Grab
• Back: Contact Details & Brief Description of our business
• Images: Ideally the main image should be the house with the pool but alternatively a lifestyle images could also be used.
Nice to have
• A creative designer!
Should not have
• Clutter & busy designs

```html
<!DOCTYPE html>
<html lang="en">
<head>
<meta charset="utf-8">
<title>Harbourline Stays – DL Flyer</title>
<link rel="stylesheet" href="https://fonts.googleapis.com/css2?family=Anton&family=Catamaran:wght@500;700&family=Lato:ital,wght@0,400;0,700;1,400&family=Michroma&family=Raleway:wght@300&display=swap">
<style>
  :root{
    --navy:#1a1548;
    --teal:#26b8a3;
    --white:#ffffff;
    --stage:#2b2b2e;
    --ink:#1f1b4d;
  }
  *{margin:0;padding:0;box-sizing:border-box}
  html,body{width:1200px;height:1051px;overflow:hidden;background:var(--stage)}
  .canvas{position:relative;width:1200px;height:1051px}

  /* ---------- Back side ---------- */
  .flyer-back{position:absolute;left:30px;top:38px;width:540px;height:761px;background:var(--navy);overflow:hidden}
  .back-art{position:absolute;left:0;top:0}
  .brand-name{font-family:"Raleway",sans-serif;font-weight:300;color:var(--white);letter-spacing:2px;text-transform:uppercase}
  .back-brand{position:absolute;left:30px;top:58px;width:190px;display:flex;align-items:center;gap:10px;font-size:20px;line-height:22px}
  .brand-dot{width:22px;height:22px;border:1.5px solid var(--white);border-radius:50%;flex:none}
  .intro{position:absolute;left:253px;top:54px;width:280px;color:var(--ink);font-family:"Lato",sans-serif}
  .intro-title{font-family:"Catamaran",sans-serif;font-weight:700;color:var(--teal);font-size:25px;line-height:30px;margin-bottom:6px;white-space:nowrap}
  .intro p{font-size:10.8px;line-height:14.5px;margin-bottom:14.5px}
  .contact{position:absolute;left:0;top:582px;width:540px;text-align:center;color:var(--white);font-family:"Lato",sans-serif}
  .contact-lead{font-style:italic;font-size:14px;line-height:19.5px}
  .contact-phone{font-family:"Catamaran",sans-serif;font-weight:700;color:var(--teal);font-size:44px;line-height:50px;margin-top:10px}
  .contact-post{font-weight:700;font-size:15px;line-height:20px;margin-top:2px}
  .contact-email{font-size:17px;line-height:22px;margin-top:8px}

  /* ---------- Front side ---------- */
  .flyer-front{position:absolute;left:619px;top:224px;width:543px;height:764px;background:var(--navy);overflow:hidden}
  .front-art{position:absolute;left:0;top:0}
  .front-brand{position:absolute;left:0;top:44px;width:543px;display:flex;justify-content:center;align-items:center;gap:10px;font-size:20px;line-height:22px}
  .headline-sub{position:absolute;left:0;top:214px;width:543px;text-align:center;color:var(--white);font-family:"Lato",sans-serif;font-size:30px;line-height:30px;text-transform:uppercase}
  .front-sign{position:absolute;left:0;top:654px;width:543px;text-align:center;font-size:22px;line-height:26px}
  .front-web{position:absolute;left:0;top:732px;width:543px;text-align:center;color:var(--white);font-family:"Michroma",sans-serif;font-size:10.5px;letter-spacing:2px}
</style>
</head>
<body>
<main class="canvas">

  <!-- Back side: description and contact -->
  <section class="flyer-back">
    <svg class="back-art" width="540" height="761" viewBox="0 0 540 761">
      <rect x="0" y="25" width="234" height="260" fill="var(--teal)"/>
      <rect x="234" y="25" width="306" height="290" fill="var(--white)"/>
      <defs>
        <radialGradient id="lounge" cx="50%" cy="45%" r="60%">
          <stop offset="0" stop-color="#c9b8a2"/><stop offset="1" stop-color="#6f6a5e"/>
        </radialGradient>
        <radialGradient id="basin" cx="50%" cy="50%" r="60%">
          <stop offset="0" stop-color="#dcdcd8"/><stop offset="1" stop-color="#9a9c98"/>
        </radialGradient>
        <radialGradient id="bedroom" cx="45%" cy="50%" r="60%">
          <stop offset="0" stop-color="#e9d35a"/><stop offset="1" stop-color="#d9c3a0"/>
        </radialGradient>
      </defs>
      <circle cx="117" cy="248" r="127" fill="var(--white)"/>
      <circle cx="117" cy="248" r="119" fill="url(#lounge)" role="img" aria-label="Photo of a vase of bird of paradise flowers on a sideboard"/>
      <circle cx="427" cy="424" r="127" fill="var(--white)"/>
      <circle cx="427" cy="424" r="119" fill="url(#bedroom)" role="img" aria-label="Photo of a made bed with yellow cushions and a patterned quilt"/>
      <circle cx="219" cy="438" r="127" fill="var(--white)"/>
      <circle cx="219" cy="438" r="119" fill="url(#basin)" role="img" aria-label="Photo of a bathroom basin with tiled wall and white orchids"/>
    </svg>

    <div class="back-brand brand-name"><span class="brand-dot"></span><span>Harbourline Stays</span></div>

    <div class="intro">
      <h2 class="intro-title">What we do differently!</h2>
      <p>Rather than relying upon a key safe or<br>a central pick-up destination,<br>a 'Harbourline Stays' staff member<br>will greet guests upon arrival.</p>
      <p>Our 'Meet &amp; Greet' service provides<br>home owners with an increased level of<br>Security &amp; also allows us to:</p>
      <p>Prepare the home for their arrival<br>(lights, heaters, music etc.)<br>Establish a rapport &amp; help facilitate future bookings<br>Reiterate their responsibilities to<br>ensure the return of their bond</p>
    </div>

    <div class="contact">
      <p class="contact-lead">If you'd like to know what your property<br>could achieve or require additional information, please contact us on:</p>
      <p class="contact-phone">(03)5900 4127</p>
      <p class="contact-post">PO Box 18, Seacliff Victoria 3907</p>
      <p class="contact-email">email: stay@harbourlinestays.com.au</p>
    </div>
  </section>

  <!-- Front side: brand, grab line and main image -->
  <section class="flyer-front">
    <svg class="front-art" width="543" height="764" viewBox="0 0 543 764">
      <defs>
        <linearGradient id="poolhouse" x1="0" y1="0" x2="0" y2="1">
          <stop offset="0" stop-color="#1a1548"/>
          <stop offset="0.35" stop-color="#2a2660"/>
          <stop offset="0.6" stop-color="#6b5a6e"/>
          <stop offset="0.8" stop-color="#3a5fa8"/>
          <stop offset="1" stop-color="#2f8ee0"/>
        </linearGradient>
      </defs>
      <rect x="0" y="270" width="543" height="360" fill="url(#poolhouse)" role="img" aria-label="Photo of a modern house at dusk with a lit swimming pool"/>
      <rect x="0" y="0" width="543" height="270" fill="var(--navy)" opacity="0"/>
      <path d="M38 585 V72 H186 M357 72 H505 V585" fill="none" stroke="var(--white)" stroke-width="1.2"/>
      <circle cx="186" cy="72" r="4.5" fill="var(--teal)"/>
      <circle cx="357" cy="72" r="4.5" fill="var(--teal)"/>
      <text x="271.5" y="209" text-anchor="middle" textLength="314" lengthAdjust="spacingAndGlyphs" font-family="Anton, sans-serif" font-size="124" fill="var(--teal)">HOLIDAY</text>
      <path d="M0 612 Q271.5 650 543 612 V764 H0 Z" fill="var(--teal)"/>
      <path d="M0 612 Q271.5 650 543 612" fill="none" stroke="var(--white)" stroke-width="3"/>
    </svg>

    <div class="front-brand brand-name"><span>Harbourline Stays</span></div>
    <h1 class="headline-sub">Rental Management<br>With a Difference</h1>
    <div class="front-sign brand-name">Harbourline Stays</div>
    <p class="front-web">harbourlinestays.com.au</p>
  </section>

</main>
</body>
</html>
```